A fantastic website for a physio

We are looking for an eye catching website which can attract as many customer as possible.
We have logo designed and ready to be used in the website.
Please use the green and blue which is used in our logo for the preferred colors.
The following are the designs that I Iike:
http://www.example-clinicone.com.au/
http://www.example-rehabtwo.com.au/
We will be having other services including massage therapy, Psychology and podiatrist. You can find information about podiatry in our condition sheet.
for the address you can put Shop 5/248 Wattlebrook Street, Kelvindale. It might change but for now you can leave it until I confirm that in the next couple of days.

Logo file can be downloaded here:
https://files.example-share.net/s/qz4mtl9wkr82bvx/Logo1511.jpg?dl=0

Target Market(s)

Infant to old people.
We speak Farsi.

Industry/Entity Type

Physical Therapy

Number of Pages Required

5+ page

Font styles to use
Serif

Colors
33a6d7
abd037
e667a6

Requirements
Must have
• Home, About , our services, Conditions we treat and contact
• For home page and contacts we would like a tab that can connect to another website(bookwell) for online booking. We would like the patient's to be able to leave us massage or leave their email for monthly news letter. For the condition we treat you can use the condition sheets I have attached. For about us and home page you can use brochure I have attached.
• The other things should have include: in-line contact form, Google Map, clinic hours, newsletter sign-up etc, schema rich contact information
• Social media connection to our Facebook, Instagram and linked in
Nice to have
• Search engine optimization for Merrylands and Parramatta physiotherapy.
• We can speak English and Farsi. So is nice to have an information tab for Farsi speaking people. I can provide you with the texts.

```html
<!DOCTYPE html>
<html lang="en">
<head>
<meta charset="utf-8">
<title>Harbourline Physiotherapy</title>
<link href="https://fonts.googleapis.com/css2?family=Montserrat:wght@400;500;600;700&display=swap" rel="stylesheet">
<style>
:root{
  --blue:#33a6d7;
  --green:#abd037;
  --pink:#e667a6;
  --pink-dark:#c9518c;
  --ink:#333;
  --panel:rgba(38,38,38,.88);
  --white:#fff;
}
*{box-sizing:border-box;margin:0;padding:0}
html,body{width:762px;height:1200px;overflow:hidden;background:#fff}
body{position:relative;font-family:'Montserrat',sans-serif;color:var(--ink)}
.abs{position:absolute}
/* header */
.site-header{left:0;top:0;width:762px;height:66px;background:#fff}
.brand{left:84px;top:14px;display:flex;align-items:center;gap:7px}
.brand-dot{width:32px;height:32px;border-radius:50%;background:var(--blue)}
.brand-name{font-size:15px;font-weight:600;color:var(--green);line-height:1.05}
.main-nav{left:294px;top:23px;display:flex;font-size:7px;font-weight:500;color:#222}
.main-nav a{display:block;height:18px;line-height:18px;padding:0 7px;text-decoration:none;color:#222}
.main-nav a.active{background:var(--green);color:#fff;padding:0 9px;margin-right:1px}
.lang{left:584px;top:23px;width:85px;height:18px;background:var(--blue);color:#fff;font-size:7px;font-weight:600;line-height:18px;padding-left:11px}
.lang svg{position:absolute;right:9px;top:7px}
/* hero */
.hero{left:0;top:66px;width:762px;height:370px}
.hero-photo{width:100%;height:100%;background:linear-gradient(100deg,#5a4538 0%,#b08a70 22%,#e8d2c0 45%,#d9cdc4 70%,#c8bfb8 100%)}
.booking{left:424px;top:97px;width:234px;height:308px;background:var(--panel);color:#fff}
.booking h2{position:absolute;left:0;top:22px;width:100%;text-align:center;font-size:14px;font-weight:500;letter-spacing:.2px}
.booking .rule{position:absolute;left:5px;right:5px;top:58px;height:1px;background:rgba(255,255,255,.25)}
.booking .label{position:absolute;left:28px;font-size:7px;font-weight:500;line-height:9px}
.booking .field{position:absolute;left:25px;width:184px;background:#fff;border:1px solid #ccc}
.btn-pink{background:var(--pink);color:#fff;font-weight:500;text-align:center;border-bottom:3px solid var(--pink-dark)}
.booking .btn-pink{position:absolute;left:25px;top:266px;width:184px;height:27px;line-height:24px;font-size:12px}
.dots{top:402px;height:2px}
/* services */
.services{left:0;top:436px;width:762px;height:321px;background:linear-gradient(90deg,#eef1f4,#f1efee 50%,#e9edf1)}
.services h2{position:absolute;top:22px;width:100%;text-align:center;color:var(--blue);font-size:16px;font-weight:700}
.services .intro{position:absolute;left:140px;top:48px;width:482px;text-align:center;font-size:6.5px;line-height:13px;color:#333}
.svc{position:absolute;top:96px;width:191px;height:205px;text-align:center}
.svc.featured{background:rgba(255,255,255,.75)}
.svc-icon{position:absolute;left:72px;top:30px;width:48px;height:50px;border-radius:8px;background:rgba(230,103,166,.18)}
.svc h3{position:absolute;top:101px;width:100%;color:var(--pink);font-size:11.5px;font-weight:700}
.svc p{position:absolute;left:8px;top:124px;width:175px;font-size:6.3px;line-height:9.2px;color:#333}
.plus{position:absolute;left:82px;top:160px;width:28px;height:28px;border-radius:50%;background:var(--pink);box-shadow:0 2px 4px rgba(0,0,0,.2)}
/* info band */
.info{left:0;top:757px;width:762px;height:217px;background:var(--blue);color:#fff}
.info h3{position:absolute;font-size:13px;font-weight:500}
.loc-list{position:absolute;left:103px;top:40px;list-style:none;font-size:6.5px;line-height:15.2px}
.loc-list li{position:relative;padding-left:19px}
.loc-list svg{position:absolute;left:1px;top:3px}
.map{left:287px;top:18px;width:211px;height:164px;background:linear-gradient(135deg,#cfe3a8 0%,#e9ece6 40%,#f3f3f1 100%);border:1px solid #fff}
.hours{position:absolute;left:513px;top:42px;font-size:7px;line-height:11.4px;border-collapse:collapse;white-space:nowrap}
.hours td{padding:0 6px}
.hours td.day{text-align:right;font-weight:600;border-right:1px solid #fff;width:71px}
.news-text{position:absolute;left:533px;top:145px;width:125px;font-size:6px;line-height:9px}
.news-input{position:absolute;left:533px;top:171px;width:122px;height:18px;background:#fff;color:#888;font-size:6.5px;line-height:18px;padding-left:8px}
.news-input svg{position:absolute;right:7px;top:4px}
/* quick contact */
.quick{left:0;top:974px;width:762px;height:161px;background:var(--green)}
.quick h2{position:absolute;top:9px;width:100%;text-align:center;color:#fff;font-size:13px;font-weight:500}
.qfield{position:absolute;background:#fff;border:1px solid #ddd;font-size:6.5px;font-weight:600;color:#444;padding:5px 9px}
.quick .btn-pink{position:absolute;left:289px;top:111px;width:184px;height:27px;line-height:24px;font-size:12px}
/* footer */
.site-footer{left:0;top:1135px;width:762px;height:65px;background:#fff}
.social{position:absolute;left:333px;top:12px;display:flex;gap:6px}
.social span{display:block;width:14px;height:14px;border-radius:50%}
.copy{position:absolute;top:32px;width:100%;text-align:center;font-size:7px;color:#444}
</style>
</head>
<body>

<header class="site-header abs">
  <div class="brand abs">
    <span class="brand-dot"></span>
    <span class="brand-name">Harbourline<br>Physiotherapy</span>
  </div>
  <nav class="main-nav abs">
    <a class="active" href="#">HOME</a>
    <a href="#">ABOUT US</a>
    <a href="#">SERVICES</a>
    <a href="#">CONDITIONS WE TREAT</a>
    <a href="#">CONTACT</a>
  </nav>
  <div class="lang abs">ENGLISH
    <svg width="6" height="4" viewBox="0 0 6 4"><path d="M0 0h6L3 4z" fill="#fff"/></svg>
  </div>
</header>

<section class="hero abs">
  <div class="hero-photo" role="img" aria-label="Photo of a man relaxing face down on a massage table while receiving a shoulder massage"></div>
</section>

<form class="booking abs">
  <h2>BOOK YOUR APPOINTMENT</h2>
  <div class="rule"></div>
  <span class="label" style="top:67px">Enter your name</span>
  <div class="field" style="top:82px;height:25px"></div>
  <span class="label" style="top:113px">Enter your Email id</span>
  <div class="field" style="top:128px;height:25px"></div>
  <span class="label" style="top:159px">Phone</span>
  <div class="field" style="top:174px;height:25px"></div>
  <span class="label" style="top:206px">Message</span>
  <div class="field" style="top:221px;height:35px"></div>
  <div class="btn-pink">Book Now</div>
</form>

<div class="dots abs" style="left:103px;width:18px;background:#222"></div>
<div class="dots abs" style="left:129px;width:18px;background:var(--pink)"></div>
<div class="dots abs" style="left:155px;width:18px;background:#222"></div>

<section class="services abs">
  <h2>OUR SERVICES</h2>
  <p class="intro">Shockwave therapy is a non surgical treatment, and works by delivering impulses of energy, targeted to specific damaged tissues. This increases the blood flow within the affected area, stimulating cell regeneration and healing, and decreasing local factors which can cause pain.</p>

  <article class="svc featured" style="left:93px">
    <div class="svc-icon" role="img" aria-label="Massage therapy line icon"></div>
    <h3>MASSAGE THERAPY</h3>
    <p>Obviously the human body is a complex structure and like many things in medicine we can provide no guarantees of effectiveness of treatment.</p>
    <div class="plus"><svg width="28" height="28" viewBox="0 0 28 28"><path d="M14 9v10M9 14h10" stroke="#fff" stroke-width="2.4" stroke-linecap="round"/></svg></div>
  </article>
  <article class="svc" style="left:284px">
    <div class="svc-icon" role="img" aria-label="Psychology consultation line icon"></div>
    <h3>PSYCHOLOGY</h3>
    <p>Obviously the human body is a complex structure and like many things in medicine we can provide no guarantees of effectiveness of treatment.</p>
  </article>
  <article class="svc" style="left:484px">
    <div class="svc-icon" role="img" aria-label="Foot line icon for podiatry"></div>
    <h3 style="top:105px">PODIATRIST</h3>
    <p>Obviously the human body is a complex structure and like many things in medicine we can provide no guarantees of effectiveness of treatment.</p>
  </article>
</section>

<section class="info abs">
  <h3 style="left:103px;top:15px">Location</h3>
  <ul class="loc-list">
    <li><svg width="6" height="8" viewBox="0 0 6 8"><path d="M3 0a3 3 0 0 1 3 3c0 2-3 5-3 5S0 5 0 3a3 3 0 0 1 3-3z" fill="#fff"/><circle cx="3" cy="3" r="1" fill="#33a6d7"/></svg>14 Tallowood Street, Kelvindale, New South Wales,<br>Australia</li>
    <li><svg width="5" height="8" viewBox="0 0 5 8"><rect x=".5" y=".5" width="4" height="7" rx=".8" fill="none" stroke="#fff"/></svg>+61.400555018</li>
    <li><svg width="8" height="6" viewBox="0 0 8 6"><rect x=".5" y=".5" width="7" height="5" fill="none" stroke="#fff"/><path d="M.5.5L4 3.5 7.5.5" fill="none" stroke="#fff"/></svg>hello@harbourline-example.com</li>
    <li><svg width="6" height="8" viewBox="0 0 6 8"><path d="M3 0a3 3 0 0 1 3 3c0 2-3 5-3 5S0 5 0 3a3 3 0 0 1 3-3z" fill="#fff"/><circle cx="3" cy="3" r="1" fill="#33a6d7"/></svg>27/3 Ridgeway Street<br>Brookmere</li>
    <li><svg width="6" height="8" viewBox="0 0 6 8"><path d="M3 0a3 3 0 0 1 3 3c0 2-3 5-3 5S0 5 0 3a3 3 0 0 1 3-3z" fill="#fff"/><circle cx="3" cy="3" r="1" fill="#33a6d7"/></svg>Shop 2, Linden Apartments<br>CNR Fern Street &amp; Elsie Street<br>Ashvale</li>
  </ul>

  <div class="map abs" role="img" aria-label="Street map of the clinic neighbourhood"></div>

  <h3 style="left:533px;top:15px">Clinic hours</h3>
  <table class="hours">
    <tr><td class="day">Monday</td><td>9:00am - 5:00pm</td></tr>
    <tr><td class="day">Tuesday</td><td>9:00am - 5:00pm</td></tr>
    <tr><td class="day">Wednesday</td><td>Closed</td></tr>
    <tr><td class="day">Thursday</td><td>9:00am - 5:00pm</td></tr>
    <tr><td class="day">Friday</td><td>9:00am - 5:00pm</td></tr>
    <tr><td class="day">Saturday &amp; Sunday</td><td>Closed</td></tr>
  </table>

  <h3 style="left:533px;top:125px">Newsletter</h3>
  <p class="news-text">Subscribe to our newsletter and get all the cool news</p>
  <div class="news-input">Enter Email
    <svg width="10" height="10" viewBox="0 0 10 10"><path d="M0 4.5L10 0 7 10 5 6z" fill="none" stroke="#222" stroke-width="1"/><path d="M5 6L10 0" stroke="#222"/></svg>
  </div>
</section>

<section class="quick abs">
  <h2>Quick Contact</h2>
  <div class="qfield" style="left:180px;top:44px;width:143px;height:19px">Name</div>
  <div class="qfield" style="left:327px;top:44px;width:144px;height:19px">Email</div>
  <div class="qfield" style="left:475px;top:44px;width:143px;height:19px">Phone</div>
  <div class="qfield" style="left:180px;top:66px;width:438px;height:35px">Message</div>
  <div class="btn-pink">Submit</div>
</section>

<footer class="site-footer abs">
  <div class="social">
    <span style="background:#3aa0dc"></span>
    <span style="background:#3b5a9a"></span>
    <span style="background:#4c7fa8"></span>
    <span style="background:var(--pink)"></span>
    <span style="background:#2b2b2b"></span>
  </div>
  <p class="copy">© 2016 .&nbsp; www.harbourline-example.com&nbsp; .&nbsp; ALL RIGHTS RESERVED</p>
</footer>

</body>
</html>
```